Website Design - TallyPorchHelpers.net

PLEASE CHECK WORD DOCUMENT ATTACHED FOR WEBSITE FLOW.

Target Market(s)

REAL ESTATE AGENTS ARE THE TARGET MARKET

Industry/Entity Type

Real Estate

Coding

Coded - Design and coding required

Number of Pages Required

4 page

Colors

Designer to choose colors to be used in the design.

Requirements
Must have
• WE LIKE RED LOGO ATTACHED
Nice to have
• PLEASE CHECK WORD DOCUMENT ATTACHED FOR WEBSITE FLOW.
Should not have

```html
<!DOCTYPE html>
<html lang="en">
<head>
<meta charset="utf-8">
<title>TallyPorchHelpers.net — Open House Marketing for Agents</title>
<link href="https://fonts.googleapis.com/css2?family=Poppins:wght@400;500;600;700&family=Roboto:wght@400;500;700&family=Dancing+Script:wght@600&display=swap" rel="stylesheet">
<style>
:root{
  --red:#e3171f;
  --red-dark:#c40f16;
  --navy:#2a2f8f;
  --navy-deep:#1f2470;
  --plum:#8b2a60;
  --ink:#1d1d28;
  --muted:#666a78;
  --paper:#f1f1f3;
  --white:#ffffff;
  --line:#dcdde3;
}
*{box-sizing:border-box;margin:0;padding:0}
html,body{width:1200px;height:4167px;overflow:hidden}
body{font-family:"Roboto",Arial,sans-serif;color:var(--ink);background:var(--white);font-size:13px;position:relative}
h1,h2,h3,h4{font-family:"Poppins",Arial,sans-serif}
.wrap{width:728px;margin:0 auto;position:relative}
section,header,footer{position:relative;width:1200px;overflow:hidden}

/* header */
.site-header{height:83px;background:var(--white);box-shadow:0 2px 6px rgba(0,0,0,.06);z-index:2}
.site-header .wrap{height:83px;display:flex;align-items:center;justify-content:space-between}
.brand{display:flex;align-items:center;gap:8px;font-family:"Poppins",sans-serif;font-weight:700;font-size:14px;color:var(--red);line-height:1.1;width:130px}
.brand-mark{width:20px;height:20px;background:var(--red);flex:none}
.main-nav{display:flex;gap:24px;font-family:"Poppins",sans-serif;font-size:10.5px;font-weight:500;letter-spacing:.4px;color:var(--ink)}
.call{display:flex;align-items:center;gap:8px}
.call small{display:block;font-size:10px;color:var(--muted)}
.call strong{display:block;font-family:"Poppins",sans-serif;color:var(--red);font-size:14px}

/* hero */
.hero{height:514px;background:var(--paper)}
.hero-photo{position:absolute;right:0;top:0;width:450px;height:514px;background:linear-gradient(160deg,#e9e4dc 0%,#cbc2b5 45%,#6a6f86 100%)}
.hero-copy{position:absolute;left:236px;top:190px;width:440px}
.hero-copy h1{font-size:34px;font-weight:700;line-height:1.18;color:var(--ink)}
.hero-copy h1 em{font-style:normal;color:var(--red)}
.hero-copy p{margin-top:12px;font-size:15px;line-height:1.45;color:#3a3d4a}

/* audience options */
.options{height:250px;background:var(--red)}
.options h2{text-align:center;color:var(--white);font-size:22px;font-weight:600;padding-top:48px}
.option-cards{position:absolute;left:236px;top:106px;width:728px;display:flex;justify-content:space-between}
.option-card{width:226px;height:144px;background:var(--white);border-radius:4px;border-bottom:5px solid var(--red);box-shadow:0 8px 20px rgba(0,0,0,.18);display:flex;flex-direction:column;align-items:center;justify-content:center;text-align:center;font-family:"Poppins",sans-serif;font-size:11.5px;font-weight:600;line-height:1.3;gap:10px}
.option-card span{display:block;font-weight:400;font-size:10.5px}

/* how it works */
.how{height:320px;background:var(--white)}
.how h2{text-align:center;font-size:24px;font-weight:600;padding-top:54px}
.steps{display:flex;justify-content:space-between;margin-top:38px}
.step{width:200px;text-align:center;position:relative}
.step-num{width:46px;height:46px;border-radius:50%;background:var(--navy);color:var(--white);font-family:"Poppins",sans-serif;font-weight:600;font-size:13px;display:flex;align-items:center;justify-content:center;margin:0 auto 14px;box-shadow:0 0 0 6px #e4e5f3}
.step p{font-size:11px;line-height:1.55;color:#444}
.step-arrow{position:absolute;top:16px;right:-50px}

/* service area */
.service-area{height:161px;background:linear-gradient(90deg,var(--plum) 0%,#5a2c78 50%,var(--navy) 100%)}
.service-area h2{text-align:center;color:var(--white);font-size:22px;font-weight:600;padding-top:38px}
.zip-form{display:flex;justify-content:center;margin-top:14px}
.zip-form input{width:375px;height:36px;border:0;padding:0 12px;font-size:11px;color:#999;font-family:"Roboto",sans-serif}
.zip-form button{width:103px;height:36px;border:0;background:var(--red);color:var(--white);font-family:"Poppins",sans-serif;font-weight:600;font-size:11px;margin-left:8px}
.service-map{height:422px;background:linear-gradient(120deg,#a9cfee 0%,#a9cfee 32%,#e8e2d0 36%,#efe9d8 70%,#dfe4cf 100%)}

/* marketing */
.marketing{height:528px;background:linear-gradient(120deg,var(--plum) 0%,#4d2d80 50%,var(--navy) 100%)}
.marketing-photo{position:absolute;right:0;top:0;width:394px;height:528px;background:linear-gradient(100deg,rgba(139,42,96,0) 0%,#b2677f 30%,#d9a48c 70%,#9a7683 100%)}
.marketing .content{position:absolute;left:236px;top:62px;width:520px;color:var(--white)}
.marketing h2{font-size:24px;font-weight:600;margin-bottom:30px}
.services{display:grid;grid-template-columns:230px 230px;column-gap:22px;row-gap:34px}
.service h3{display:flex;align-items:center;gap:10px;font-size:14px;font-weight:600;margin-bottom:10px}
.service-icon{width:32px;height:32px;border:2px solid var(--white);border-radius:50%;display:flex;align-items:center;justify-content:center;font-size:9px;font-weight:700;flex:none}
.service p{font-size:11px;line-height:1.6;opacity:.9}

/* pricing */
.pricing{height:611px;background:var(--paper)}
.pricing h2{text-align:center;font-size:24px;font-weight:600;padding-top:60px}
.plans{position:absolute;left:244px;top:117px;width:726px;display:flex;gap:18px;align-items:flex-start}
.plan{width:128px;height:425px;background:var(--white);border-radius:3px;box-shadow:0 4px 14px rgba(0,0,0,.1);text-align:center;padding:18px 10px 0;position:relative;overflow:hidden}
.plan h3{font-size:13px;font-weight:600}
.price{width:56px;height:56px;border-radius:50%;background:var(--red);color:var(--white);font-family:"Poppins",sans-serif;font-weight:700;font-size:19px;display:flex;align-items:center;justify-content:center;margin:14px auto 18px}
.price sup{font-size:10px}
.plan ul{list-style:none;text-align:left;font-size:10px;line-height:1.45;color:#555}
.plan li{display:flex;gap:5px;margin-bottom:14px}
.plan li svg{flex:none;margin-top:2px}
.plan .btn{display:block;background:var(--navy);color:var(--white);font-family:"Poppins",sans-serif;font-weight:600;font-size:10px;padding:11px 4px;border-radius:2px;margin-top:4px}
.plan .note{font-size:8.5px;color:#777;line-height:1.4;margin-top:14px}
.plan.featured{margin-top:-12px;height:437px;padding:0 10px}
.plan.featured .top{background:var(--red);margin:0 -10px;padding:18px 0 14px}
.plan.featured h3{color:var(--white)}
.plan.featured .price{background:var(--navy);margin:10px auto 0}
.plan.featured ul{margin-top:18px}
.plan.featured .btn{background:var(--red)}
.plan.custom .btn{font-size:9px;padding:7px 4px;line-height:1.35}

/* faq */
.faq{height:431px;background:linear-gradient(180deg,#7e2b66 0%,#4f2c7f 55%,var(--navy) 100%)}
.faq h2{text-align:center;color:var(--white);font-size:22px;font-weight:600;padding-top:56px}
.faq-cols{position:absolute;left:236px;top:118px;width:728px;display:flex;justify-content:space-between}
.faq-col{width:347px;display:flex;flex-direction:column;gap:8px}
.faq-item{height:36px;background:var(--white);display:flex;align-items:center;justify-content:space-between;padding:0 12px;font-size:11.5px;color:var(--ink)}
.faq-item b{font-size:16px;font-weight:400}
.faq-item.open{background:var(--red);color:var(--white)}
.faq-answer{background:var(--white);padding:12px;font-size:10.5px;line-height:1.6;color:#555;margin-top:-8px}

/* testimonials */
.testimonials{height:491px;background:var(--white)}
.testimonials h2{text-align:center;font-size:24px;font-weight:600;padding-top:60px}
.quotes{position:absolute;left:236px;top:120px;width:728px;display:flex;justify-content:space-between}
.quote{width:345px;text-align:center}
.quote-body{position:relative;padding:0 34px}
.quote .mark{position:absolute;font-family:"Poppins",sans-serif;font-size:44px;font-weight:700;color:var(--red);line-height:1}
.quote .mark.open{left:0;top:-8px}
.quote .mark.close{right:0;bottom:-26px}
.quote p{font-size:11px;line-height:1.7;color:#555}
.avatar{width:56px;height:56px;border-radius:50%;background:linear-gradient(135deg,#d8d1cb,#9a9aa8);margin:26px auto 8px;border:3px solid var(--white);box-shadow:0 2px 8px rgba(0,0,0,.15)}
.quote cite{font-family:"Dancing Script",cursive;font-style:normal;font-size:22px;color:var(--ink)}
.dots{position:absolute;left:0;right:0;top:393px;display:flex;justify-content:center;gap:7px}
.dots i{width:8px;height:8px;border-radius:50%;background:#cfd0d8}
.dots i.on{background:var(--red)}

/* newsletter + footer */
.newsletter{height:18px;background:var(--white)}
.newsletter::before{content:"";position:absolute;left:0;right:0;top:9px;height:3px;background:var(--red)}
.newsletter-btn{position:absolute;left:439px;top:3799px;width:325px;height:42px;border-radius:21px;background:var(--red);color:var(--white);font-family:"Poppins",sans-serif;font-weight:600;font-size:13px;display:flex;align-items:center;justify-content:center;letter-spacing:.3px;z-index:3}
.site-footer{height:309px;background:var(--navy-deep);color:var(--white)}
.footer-cols{position:absolute;left:236px;top:60px;width:728px;display:grid;grid-template-columns:228px 208px 125px 167px}
.footer-cols > div{padding-right:16px}
.footer-cols > div:last-child{padding-right:0}
.footer-cols h4{font-size:11.5px;font-weight:600;margin-bottom:12px;letter-spacing:.3px}
.footer-cols p,.footer-cols li{font-size:10.5px;line-height:1.6;opacity:.85;list-style:none}
.socials{display:flex;gap:6px;margin-top:12px}
.socials i{width:22px;height:22px;border:1.5px solid var(--white);border-radius:50%}
.contact-form{display:flex;flex-direction:column;gap:6px}
.contact-form span{height:22px;background:var(--white);color:#999;font-size:9.5px;padding:5px 8px}
.contact-form span.msg{height:36px}
.contact-form b{align-self:flex-end;background:var(--red);font-family:"Poppins",sans-serif;font-size:9.5px;padding:7px 14px;font-weight:600}
.copyright{height:28px;background:#171a55;color:rgba(255,255,255,.75);font-size:10px}
.copyright .wrap{height:28px;display:flex;align-items:center;justify-content:space-between}
</style>
</head>
<body>

<header class="site-header">
  <div class="wrap">
    <div class="brand"><span class="brand-mark"></span>Tally Porch Helpers</div>
    <nav class="main-nav"><span>HOW IT WORKS</span><span>SERVICE AREA</span><span>PRICING</span><span>ABOUT US</span><span>FAQ</span></nav>
    <div class="call">
      <svg width="22" height="22" viewBox="0 0 24 24"><path fill="#e3171f" d="M6.6 10.8a15 15 0 0 0 6.6 6.6l2.2-2.2c.3-.3.7-.4 1-.2 1.1.4 2.3.6 3.6.6.6 0 1 .4 1 1V20c0 .6-.4 1-1 1A17 17 0 0 1 3 4c0-.6.4-1 1-1h3.5c.6 0 1 .4 1 1 0 1.3.2 2.5.6 3.6.1.3 0 .7-.2 1z"/></svg>
      <div><small>Call Or Text Us</small><strong>1-555-014-2290</strong></div>
    </div>
  </div>
</header>

<section class="hero">
  <div class="hero-photo" role="img" aria-label="Photo of a smiling couple stepping through the front door of a bright home"></div>
  <div class="hero-copy">
    <h1>Helping <em>agents</em><br>save time and money.</h1>
    <p>We place signs and boost foot traffic to<br>your open houses using proven marketing techniques.</p>
  </div>
</section>

<section class="options">
  <h2>Choose The Option Below That Best Describes You</h2>
  <div class="option-cards">
    <div class="option-card">
      <svg width="30" height="30" viewBox="0 0 24 24"><path fill="#e3171f" d="M3 21V6l6-3v18zm8 0V9h10v12zm-6-13h2v2H5zm0 4h2v2H5zm0 4h2v2H5zm8-4h2v2h-2zm4 0h2v2h-2zm-4 4h2v2h-2zm4 0h2v2h-2z"/></svg>
      <div><span>I'M A</span>FULL ON BROKERAGE</div>
    </div>
    <div class="option-card">
      <svg width="32" height="30" viewBox="0 0 26 24"><g fill="#e3171f"><circle cx="13" cy="7" r="3.5"/><circle cx="5.5" cy="9" r="2.6"/><circle cx="20.5" cy="9" r="2.6"/><path d="M7 20c0-4 2.7-7 6-7s6 3 6 7zM1 19c0-3 2-5 4.5-5 1 0 1.8.3 2.4.8C7 16 6.5 17.5 6.5 19zM25 19c0-3-2-5-4.5-5-1 0-1.8.3-2.4.8.9 1.2 1.4 2.7 1.4 4.2z"/></g></svg>
      <div><span>I'M AN</span>IND. BROKER WITH A TEAM</div>
    </div>
    <div class="option-card">
      <svg width="28" height="30" viewBox="0 0 22 24"><g fill="#e3171f"><rect x="2" y="1" width="2.4" height="22"/><rect x="4.4" y="4" width="16" height="2"/><rect x="7" y="7" width="12" height="9"/></g></svg>
      <div><span>I NEED</span>SIGN PLACEMENT ASAP</div>
    </div>
  </div>
</section>

<section class="how">
  <div class="wrap">
    <h2>How It Works</h2>
    <div class="steps">
      <div class="step">
        <div class="step-num">01</div>
        <p>We boost Foot Traffic To Your Open House Using Proven Marketing Channels: Social Feed Ads, SMS Notifications, Voice Broadcasts and Email Notifications</p>
        <svg class="step-arrow" width="44" height="12" viewBox="0 0 44 12"><path d="M0 6h40m-5-5 5 5-5 5" stroke="#333" stroke-width="1.2" fill="none"/></svg>
      </div>
      <div class="step">
        <div class="step-num">02</div>
        <p>We Place Open House Signs Strategically In The Surrounding Area</p>
        <svg class="step-arrow" width="44" height="12" viewBox="0 0 44 12"><path d="M0 6h40m-5-5 5 5-5 5" stroke="#333" stroke-width="1.2" fill="none"/></svg>
      </div>
      <div class="step">
        <div class="step-num">03</div>
        <p>Store custom signs for you if needed</p>
      </div>
    </div>
  </div>
</section>

<section class="service-area">
  <h2>Service Area</h2>
  <form class="zip-form"><input type="text" value="Enter Your Open House Zipcode" aria-label="Open house zipcode"><button type="button">SUBMIT</button></form>
</section>
<section class="service-map" role="img" aria-label="Map of the coastal service region with cities and highways"></section>

<section class="marketing">
  <div class="marketing-photo" role="img" aria-label="Photo of an excited woman shouting into a megaphone"></div>
  <div class="content">
    <h2>Marketing Services</h2>
    <div class="services">
      <div class="service">
        <h3><span class="service-icon">SMS</span>SMS</h3>
        <p>We will send a Text Message to all the people that live in the surrounding area of your Open House to let them know there is a home for sale in their neighborhood and to let anyone that they may know looking to purchase a new home to come check it out!</p>
      </div>
      <div class="service">
        <h3><span class="service-icon"><svg width="14" height="11" viewBox="0 0 14 11"><path d="M1 1h12v9H1zM1 1l6 5 6-5" stroke="#fff" stroke-width="1.4" fill="none"/></svg></span>EMAIL</h3>
        <p>We will send an Email Message to all the people that live in the surrounding area of your Open House to let them know there is a home for sale in their neighborhood and to let anyone that they may know looking to purchase a new home to come check it out!</p>
      </div>
      <div class="service">
        <h3><span class="service-icon"><svg width="14" height="14" viewBox="0 0 14 14"><rect x="1" y="1" width="12" height="12" stroke="#fff" stroke-width="1.4" fill="none"/></svg></span>SOCIAL FEED ADS</h3>
        <p>We will place a Social Ad in the news feeds of all the people that live in the surrounding area of your Open House to let them know there is a home for sale in their neighborhood and to let anyone that they may know looking to purchase a new home to come check it out!</p>
      </div>
      <div class="service">
        <h3><span class="service-icon"><svg width="10" height="15" viewBox="0 0 10 15"><rect x="2.5" y="1" width="5" height="8" rx="2.5" fill="#fff"/><path d="M1 7a4 4 0 0 0 8 0M5 11v3" stroke="#fff" stroke-width="1.3" fill="none"/></svg></span>VOICE BROADCAST</h3>
        <p>We will send a voice broadcast to all the people that live in the surrounding area of your Open House to let them know there is a home for sale in their neighborhood and to let anyone that they may know looking to purchase a new home to come check it out!</p>
      </div>
    </div>
  </div>
</section>

<section class="pricing">
  <h2>Choose Your Package</h2>
  <div class="plans">
    <div class="plan">
      <h3>5 SIGNS</h3><div class="price"><sup>$</sup>49</div>
      <ul>
        <li><svg width="9" height="9" viewBox="0 0 9 9"><rect width="9" height="9" fill="#2a2f8f"/><path d="M2 4.5l1.8 1.8L7 3" stroke="#fff" stroke-width="1.2" fill="none"/></svg>Place signs strategically in best areas according to where the open house is located</li>
        <li><svg width="9" height="9" viewBox="0 0 9 9"><rect width="9" height="9" fill="#2a2f8f"/><path d="M2 4.5l1.8 1.8L7 3" stroke="#fff" stroke-width="1.2" fill="none"/></svg>Pick up the signs after the open house</li>
        <li><svg width="9" height="9" viewBox="0 0 9 9"><rect width="9" height="9" fill="#2a2f8f"/><path d="M2 4.5l1.8 1.8L7 3" stroke="#fff" stroke-width="1.2" fill="none"/></svg>Store custom signs for you if needed</li>
      </ul>
      <span class="btn">SIGN UP</span>
      <p class="note">Sign Up For A Subscription And Get These Marketing Services For Free</p>
    </div>
    <div class="plan">
      <h3>10 SIGNS</h3><div class="price"><sup>$</sup>59</div>
      <ul>
        <li><svg width="9" height="9" viewBox="0 0 9 9"><rect width="9" height="9" fill="#2a2f8f"/><path d="M2 4.5l1.8 1.8L7 3" stroke="#fff" stroke-width="1.2" fill="none"/></svg>Place signs strategically in best areas according to where the open house is located</li>
        <li><svg width="9" height="9" viewBox="0 0 9 9"><rect width="9" height="9" fill="#2a2f8f"/><path d="M2 4.5l1.8 1.8L7 3" stroke="#fff" stroke-width="1.2" fill="none"/></svg>Pick up the signs after the open house</li>
        <li><svg width="9" height="9" viewBox="0 0 9 9"><rect width="9" height="9" fill="#2a2f8f"/><path d="M2 4.5l1.8 1.8L7 3" stroke="#fff" stroke-width="1.2" fill="none"/></svg>Store custom signs for you if needed</li>
      </ul>
      <span class="btn">SIGN UP</span>
      <p class="note">Sign Up For A Subscription And Get These Marketing Services For Free</p>
    </div>
    <div class="plan featured">
      <div class="top"><h3>15 SIGNS</h3><div class="price"><sup>$</sup>69</div></div>
      <ul>
        <li><svg width="9" height="9" viewBox="0 0 9 9"><rect width="9" height="9" fill="#e3171f"/><path d="M2 4.5l1.8 1.8L7 3" stroke="#fff" stroke-width="1.2" fill="none"/></svg>Place signs strategically in best areas according to where the open house is located</li>
        <li><svg width="9" height="9" viewBox="0 0 9 9"><rect width="9" height="9" fill="#e3171f"/><path d="M2 4.5l1.8 1.8L7 3" stroke="#fff" stroke-width="1.2" fill="none"/></svg>Pick up the signs after the open house</li>
        <li><svg width="9" height="9" viewBox="0 0 9 9"><rect width="9" height="9" fill="#e3171f"/><path d="M2 4.5l1.8 1.8L7 3" stroke="#fff" stroke-width="1.2" fill="none"/></svg>Store custom signs for you if needed</li>
      </ul>
      <span class="btn">SIGN UP</span>
      <p class="note">Sign Up For A Subscription And Get These Marketing Services For Free</p>
    </div>
    <div class="plan">
      <h3>20 SIGNS</h3><div class="price"><sup>$</sup>79</div>
      <ul>
        <li><svg width="9" height="9" viewBox="0 0 9 9"><rect width="9" height="9" fill="#2a2f8f"/><path d="M2 4.5l1.8 1.8L7 3" stroke="#fff" stroke-width="1.2" fill="none"/></svg>Place signs strategically in best areas according to where the open house is located</li>
        <li><svg width="9" height="9" viewBox="0 0 9 9"><rect width="9" height="9" fill="#2a2f8f"/><path d="M2 4.5l1.8 1.8L7 3" stroke="#fff" stroke-width="1.2" fill="none"/></svg>Pick up the signs after the open house</li>
        <li><svg width="9" height="9" viewBox="0 0 9 9"><rect width="9" height="9" fill="#2a2f8f"/><path d="M2 4.5l1.8 1.8L7 3" stroke="#fff" stroke-width="1.2" fill="none"/></svg>Store custom signs for you if needed</li>
      </ul>
      <span class="btn">SIGN UP</span>
      <p class="note">Sign Up For A Subscription And Get These Marketing Services For Free</p>
    </div>
    <div class="plan custom">
      <h3>25+ SIGNS</h3><div class="price" style="visibility:hidden"></div>
      <ul>
        <li><svg width="9" height="9" viewBox="0 0 9 9"><rect width="9" height="9" fill="#2a2f8f"/><path d="M2 4.5l1.8 1.8L7 3" stroke="#fff" stroke-width="1.2" fill="none"/></svg>Place signs strategically in best areas according to where the open house is located</li>
        <li><svg width="9" height="9" viewBox="0 0 9 9"><rect width="9" height="9" fill="#2a2f8f"/><path d="M2 4.5l1.8 1.8L7 3" stroke="#fff" stroke-width="1.2" fill="none"/></svg>Pick up the signs after the open house</li>
        <li><svg width="9" height="9" viewBox="0 0 9 9"><rect width="9" height="9" fill="#2a2f8f"/><path d="M2 4.5l1.8 1.8L7 3" stroke="#fff" stroke-width="1.2" fill="none"/></svg>Store custom signs for you if needed</li>
      </ul>
      <span class="btn">CLICK HERE TO<br>CREATE CUSTOM PKG</span>
      <p class="note">Sign Up For A Subscription And Get These Marketing Services For Free</p>
    </div>
  </div>
</section>

<section class="faq">
  <h2>Frequently Asked Questions</h2>
  <div class="faq-cols">
    <div class="faq-col">
      <div class="faq-item">Vestibulum sed felis a ante suscipit auctor<b>+</b></div>
      <div class="faq-item">Sed ullamcorper augue ut facilisis condimentum<b>+</b></div>
      <div class="faq-item">Curabitur at ligula sed velit feugiat pellentesque<b>+</b></div>
      <div class="faq-item">Nam vitae velit non augue ultricies laoreet<b>+</b></div>
    </div>
    <div class="faq-col">
      <div class="faq-item">Curabitur at ligula sed velit feugiat pellentesque<b>+</b></div>
      <div class="faq-item open">Lorem ipsum used in various languages for layouts<b>−</b></div>
      <div class="faq-answer">In publishing and graphic design, lorem ipsum is a placeholder text commonly used to demonstrate the visual form of a document. In publishing graphic design, lorem ipsum is a placeholder text commonly used to demonstrate the visual form of a document.</div>
      <div class="faq-item">Sed ullamcorper augue ut facilisis condimentum<b>+</b></div>
      <div class="faq-item">Nam vitae velit non augue ultricies laoreet<b>+</b></div>
    </div>
  </div>
</section>

<section class="testimonials">
  <h2>Clients Testimonials</h2>
  <div class="quotes">
    <div class="quote">
      <div class="quote-body">
        <span class="mark open">“</span><span class="mark close">”</span>
        <p>In publishing and graphic design, lorem ipsum is a placeholder text commonly used to demonstrate the visual. In publishing graphic design, lorem ipsum is a placeholder text commonly used to demonstrate the visual form of a document. Demonstrate the visual. In publishing graphic design lorem ipsum is a text commonly used to demonstrate the visual form of a document.</p>
      </div>
      <div class="avatar" role="img" aria-label="Client portrait"></div>
      <cite>Marla Quinn</cite>
    </div>
    <div class="quote">
      <div class="quote-body">
        <span class="mark open">“</span><span class="mark close">”</span>
        <p>In publishing and graphic design, lorem ipsum is a placeholder text commonly used to demonstrate the visual. In publishing graphic design, lorem ipsum is a placeholder text commonly used to demonstrate the visual form of a document. Demonstrate the visual. In publishing graphic design lorem ipsum is a text commonly used to demonstrate the visual form of a document.</p>
      </div>
      <div class="avatar" role="img" aria-label="Client portrait"></div>
      <cite>Dorian Vey</cite>
    </div>
  </div>
  <div class="dots"><i></i><i></i><i class="on"></i><i></i><i></i></div>
</section>

<div class="newsletter-btn">SUBSCRIBE TO OUR NEWSLETTER</div>
<section class="newsletter"></section>

<footer class="site-footer">
  <div class="footer-cols">
    <div>
      <h4>ABOUT TALLY PORCH HELPERS</h4>
      <p>Owned and operated by a highly experienced Home Sales Expert Marketer and a Top Realtor, we help agents leverage their time and skills to increase production at an affordable price with impeccable support!</p>
      <div class="socials"><i></i><i></i><i></i><i></i><i></i></div>
    </div>
    <div>
      <h4>CONTACT INFORMATION</h4>
      <p>4410 Larkmoor Lane,<br>Suite 12, Ferncrest, TX 70000</p>
      <p style="margin-top:12px">Call Or Text Us:<br>1-555-014-2290</p>
      <p style="margin-top:12px">Email Us:<br>info@tallyporchhelpers.net</p>
    </div>
    <div>
      <h4>QUICK LINKS</h4>
      <ul><li>How It Works</li><li>Service Area</li><li>Pricing</li><li>About Us</li><li>FAQ</li></ul>
    </div>
    <div>
      <h4>CONTACT US RIGHT NOW</h4>
      <div class="contact-form"><span>Name</span><span>Email Address</span><span>Phone</span><span class="msg">Message</span><b>SEND A MESSAGE</b></div>
    </div>
  </div>
</footer>
<div class="copyright"><div class="wrap"><span>Copyright © 2018 Tally Porch Helpers</span><span>Terms of Use / Privacy / Sitemap</span></div></div>

</body>
</html>
```